Web Developer Needs a Business Card Design

I need a personal business card design that represents me as a web developer for potential employers. I would like the background to be a dark color on the front for contrast with my logo and name. The back will have all my information along with a smaller version of the logo. I want something with a modern look and feel, not too conservative. This will be used for potential employers and freelance work.

Industry/Entity Type

Business

Contact Information for Business Card

Front should have my logo and name. The back should have all my personal information which would include: name: Tom Varulek, phone: 570-614-3098, email: tomvarulek@quillbox.net, website url: www.tomvarulek.net, logo, web developer.

Font styles to use
Sans Serif

Requirements
Must have
• Must include my logo. The color palette base color will be the logo color.

```html
<!DOCTYPE html>
<html lang="en">
<head>
<meta charset="utf-8">
<title>Tom Varulek – Business Card</title>
<link rel="stylesheet" href="https://fonts.googleapis.com/css2?family=Open+Sans:wght@400;600;700&display=swap">
<style>
  :root {
    --backdrop: #3b3431;
    --card: #161616;
    --card-edge: #1d1d1d;
    --teal: #63c6b0;
    --ink: #ffffff;
    --ink-soft: #e4e4e4;
    --mark-faint: #263230;
  }
  * { box-sizing: border-box; margin: 0; padding: 0; }
  html, body {
    width: 1200px;
    height: 844px;
    overflow: hidden;
  }
  body {
    background: var(--backdrop);
    font-family: "Open Sans", Arial, sans-serif;
    position: relative;
  }
  .card {
    position: absolute;
    top: 273px;
    width: 520px;
    height: 297px;
    background: linear-gradient(100deg, var(--card) 0%, var(--card) 70%, #2a2a2a 100%);
    overflow: hidden;
    box-shadow: 0 10px 30px rgba(0,0,0,0.45);
  }
  .card--details { left: 60px; }
  .card--identity {
    left: 620px;
    background: radial-gradient(circle at 50% 38%, #232323 0%, var(--card) 60%);
  }

  /* details side */
  .band {
    position: absolute;
    left: 0;
    width: 100%;
    height: 14px;
    background: var(--teal);
  }
  .band--top { top: 0; }
  .band--bottom { bottom: 0; }
  .faint-ring {
    position: absolute;
    left: 96px;
    top: 42px;
    width: 212px;
    height: 212px;
  }
  .holder {
    position: absolute;
    left: 168px;
    top: 76px;
  }
  .holder__name {
    font-weight: 700;
    font-size: 17px;
    letter-spacing: 0.5px;
    color: var(--ink);
    line-height: 1.2;
  }
  .holder__rule {
    height: 1px;
    width: 150px;
    background: var(--teal);
    margin: 3px 0 2px;
  }
  .holder__role {
    font-size: 12px;
    color: var(--ink-soft);
  }
  .contact {
    position: absolute;
    right: 196px;
    top: 174px;
    text-align: right;
    list-style: none;
    font-size: 13px;
    line-height: 17px;
    color: var(--ink-soft);
  }

  /* identity side */
  .tab {
    position: absolute;
    width: 22px;
    height: 44px;
    background: var(--teal);
  }
  .tab--top-right { right: 0; top: 20px; }
  .tab--mid-left { left: 0; top: 150px; }
  .brand {
    position: absolute;
    left: 0;
    top: 58px;
    width: 100%;
    text-align: center;
  }
  .brand__ring { display: block; margin: 0 auto 22px; }
  .brand__name {
    font-weight: 700;
    font-size: 20px;
    color: var(--ink);
  }
</style>
</head>
<body>
  <section class="card card--details" aria-label="Card back with contact details">
    <div class="band band--top"></div>
    <svg class="faint-ring" viewBox="0 0 212 212" aria-hidden="true">
      <circle cx="106" cy="106" r="98" fill="none" stroke="var(--mark-faint)" stroke-width="12"/>
    </svg>
    <div class="holder">
      <p class="holder__name">TOM VARULEK</p>
      <div class="holder__rule"></div>
      <p class="holder__role">Front-End Developer</p>
    </div>
    <ul class="contact">
      <li>570-614-3098</li>
      <li>tomvarulek@quillbox.net</li>
      <li>www.tomvarulek.net</li>
    </ul>
    <div class="band band--bottom"></div>
  </section>

  <section class="card card--identity" aria-label="Card front with name">
    <div class="tab tab--top-right"></div>
    <div class="tab tab--mid-left"></div>
    <div class="brand">
      <svg class="brand__ring" width="116" height="116" viewBox="0 0 116 116" aria-hidden="true">
        <circle cx="58" cy="58" r="53" fill="none" stroke="var(--teal)" stroke-width="6"/>
      </svg>
      <p class="brand__name">Tom Varulek</p>
    </div>
  </section>
</body>
</html>
```